full stationary design for a modern sleek design company

we are a design company that does modern minimalistic interior design works as well as other design services for high end clients.
we need a full stationary design including and not limited to (double sided business card, letter head, envelopes, documents folder...etc) that reflects the modern style design we do.
sleek modern and minimalistic is the requirements.
Updates

please use the latest attached files as there was a slight modification on the logo Added Wednesday, March 1, 2017

minor update on the logo files in JPG and PSD has been updated kindly follow the new attachments. Added Thursday, March 2, 2017

Target Market(s)

modern minimalist clients

Industry/Entity Type

Design Agency

Requirements
Must have
• the logo
Nice to have
• i like the colors in the colored 3D logo attached
Should not have
• too many colors

```html
<!DOCTYPE html>
<html lang="en">
<head>
<meta charset="utf-8">
<title>Linea Atelier – Business Card</title>
<link rel="stylesheet" href="https://fonts.googleapis.com/css2?family=Source+Sans+3:wght@400;600&display=swap">
<style>
  :root {
    --backdrop: #5a4838;
    --paper: #ffffff;
    --brand-orange: #f7931e;
    --ink: #333333;
    --ink-soft: #444444;
    --rule: #3a3a3a;
  }
  * { margin: 0; padding: 0; box-sizing: border-box; }
  html, body { width: 1200px; height: 987px; overflow: hidden; }
  body {
    background: var(--backdrop);
    font-family: "Source Sans 3", Arial, sans-serif;
    position: relative;
  }
  .card {
    position: absolute;
    left: 293px;
    width: 615px;
    height: 350px;
  }
  .card--front { top: 130px; background: var(--paper); }
  .card--back { top: 505px; background: var(--brand-orange); }

  .brand {
    display: flex;
    align-items: center;
    gap: 10px;
    font-weight: 600;
    font-size: 34px;
    letter-spacing: 2px;
    text-transform: uppercase;
    color: var(--ink);
    line-height: 1;
  }
  .brand__mark { width: 26px; height: 26px; background: var(--brand-orange); }
  .card--back .brand__mark { background: var(--ink); }
  .card--front .brand { position: absolute; right: 38px; top: 56px; }
  .card--back .brand { position: absolute; left: 0; right: 0; top: 155px; justify-content: center; }

  .holder { position: absolute; left: 29px; top: 192px; right: 38px; }
  .holder__name { color: var(--brand-orange); font-weight: 600; font-size: 22px; line-height: 1; }
  .holder__role {
    display: flex; align-items: center; gap: 2px;
    margin-top: 7px; font-size: 16px; color: var(--ink); line-height: 1;
  }
  .holder__role::after { content: ""; flex: 1; height: 1px; background: var(--rule); margin-top: 4px; }

  .contact { position: absolute; left: 29px; top: 254px; list-style: none; font-size: 16px; color: var(--ink-soft); }
  .contact li { display: flex; align-items: center; gap: 8px; height: 23.5px; }
  .contact svg { width: 14px; height: 14px; fill: var(--brand-orange); flex: none; }

  .address {
    position: absolute; right: 38px; top: 254px;
    font-style: normal; text-align: right; font-size: 16px; color: var(--ink-soft); line-height: 23.5px;
  }

  .edge-band { position: absolute; left: 0; right: 0; bottom: 0; height: 11px; display: flex; }
  .edge-band__dark { width: 19px; background: var(--ink); }
  .edge-band__gap { width: 3px; background: var(--paper); }
  .edge-band__orange { flex: 1; background: var(--brand-orange); }
</style>
</head>
<body>
  <section class="card card--front">
    <div class="brand"><span class="brand__mark"></span>Linea Atelier</div>

    <div class="holder">
      <p class="holder__name">NORA VANCE</p>
      <p class="holder__role">CEO&amp;Founder</p>
    </div>

    <ul class="contact">
      <li>
        <svg viewBox="0 0 24 24" aria-hidden="true"><path d="M6.6 10.8a15.1 15.1 0 0 0 6.6 6.6l2.2-2.2c.3-.3.7-.4 1-.2 1.1.4 2.3.6 3.6.6.6 0 1 .4 1 1V20c0 .6-.4 1-1 1A17 17 0 0 1 3 4c0-.6.4-1 1-1h3.5c.6 0 1 .4 1 1 0 1.3.2 2.5.6 3.6.1.3 0 .7-.2 1z"/></svg>
        (555) 210 4817
      </li>
      <li>
        <svg viewBox="0 0 24 24" aria-hidden="true"><path d="M7 1h10a2 2 0 0 1 2 2v18a2 2 0 0 1-2 2H7a2 2 0 0 1-2-2V3a2 2 0 0 1 2-2zm0 3v14h10V4zm5 15.5a1.2 1.2 0 1 0 0 2.4 1.2 1.2 0 0 0 0-2.4z"/></svg>
        (555) 362 9051
      </li>
      <li>
        <svg viewBox="0 0 24 24" aria-hidden="true"><path d="M2 5h20v14H2zm2 2v.4l8 5 8-5V7zm0 2.8V17h16V9.8l-8 5z"/></svg>
        nora@lineaatelier.com
      </li>
    </ul>

    <address class="address">
      1420 Harbor Crest Road<br>
      Fairview, Oregon 97024<br>
      www.lineaatelier.com
    </address>

    <div class="edge-band">
      <span class="edge-band__dark"></span><span class="edge-band__gap"></span><span class="edge-band__orange"></span>
    </div>
  </section>

  <section class="card card--back">
    <div class="brand"><span class="brand__mark"></span>Linea Atelier</div>
  </section>
</body>
</html>
```